Tidewell Homecare

I am looking to have a website designed for a housekeeping company that looks similar to this one. https://marloweshomecare.example/

I need 5 websites designed but will start with this one to see how I like it.

Industry/Entity Type

House Cleaning

Coding

Coded - Design and coding required

Number of Pages Required

5+ page

Font styles to use
Serif
Script

Colors
ffffff
fdf9cf
fbf289
fbee3f
d6edf3
86cae7
33a6d7
edf1f8
cedeed

```html
<!DOCTYPE html>
<html lang="en">
<head>
<meta charset="utf-8">
<title>Tidewell Homecare</title>
<link href="https://fonts.googleapis.com/css2?family=Montserrat:wght@400;500;600;700;800&family=Mulish:wght@400;600;700;800&family=Arimo:wght@400&display=swap" rel="stylesheet">
<style>
:root{
  --blue:#2f95d2;
  --blue-light:#5fb6e0;
  --yellow:#f9e93a;
  --yellow-soft:#fbf289;
  --ink:#1f2226;
  --text:#4a4d52;
  --muted:#6b6f75;
  --white:#ffffff;
  --line:#cfd3d8;
  --pale:#edf1f8;
}
*{margin:0;padding:0;box-sizing:border-box}
html,body{width:1200px;height:3410px;overflow:hidden;background:var(--white)}
body{position:relative;font-family:'Mulish',sans-serif;color:var(--text)}
.abs{position:absolute}

/* header */
.site-header{left:0;top:0;width:1200px;height:98px;background:var(--white)}
.brand{left:49px;top:31px;font-family:'Montserrat',sans-serif;font-weight:700;font-size:23px;letter-spacing:1px;color:var(--blue);text-transform:uppercase}
.main-nav a{position:absolute;top:37px;font-family:'Montserrat',sans-serif;font-size:16px;letter-spacing:.6px;color:#6f7378;text-decoration:none;text-transform:uppercase}
.main-nav a.active{color:var(--blue)}
.phone-btn{left:974px;top:22px;width:189px;height:47px;border-radius:24px;background:var(--yellow);display:flex;align-items:center;justify-content:center;gap:6px;font-family:'Montserrat',sans-serif;font-weight:700;font-size:19px;color:#3a3218}

/* hero */
.hero{left:0;top:98px;width:1200px;height:609px;background:linear-gradient(100deg,#8e8d88 0%,#c9c6bf 30%,#d8d3c4 55%,#b8b3a8 75%,#e6e4de 100%)}
.hero-frame{left:377px;top:245px;width:479px;height:293px;border:2px solid rgba(255,255,255,.9)}
.hero-panel{left:387px;top:256px;width:459px;height:270px;background:rgba(249,233,58,.88);text-align:center;padding-top:40px}
.hero-panel h1{font-family:'Montserrat',sans-serif;font-weight:700;font-size:31px;line-height:40px;letter-spacing:1px;color:#2a2a22;text-transform:uppercase}
.hero-panel p{margin:14px auto 0;width:320px;font-size:16.5px;line-height:25px;color:#3a3828}
.hero-arrow{top:345px}

/* service cards */
.card{top:762px;width:437px;height:308px;text-align:center;background:var(--white)}
.card.commercial{left:142px;border:2px solid var(--yellow)}
.card.residential{left:619px;border:2px solid var(--blue-light)}
.card svg{position:absolute;left:50%;top:31px;transform:translateX(-50%)}
.card h2{position:absolute;top:109px;width:100%;font-family:'Montserrat',sans-serif;font-weight:500;font-size:22px;letter-spacing:1.6px;color:#2b2d31;text-transform:uppercase}
.card p{position:absolute;top:150px;left:40px;right:40px;font-size:14.5px;line-height:24.5px;color:#55585d}
.btn{display:flex;align-items:center;justify-content:center;border-radius:26px;font-family:'Montserrat',sans-serif;font-weight:700;font-size:14px;letter-spacing:1px;text-transform:uppercase}
.card .btn{position:absolute;top:236px;left:50%;transform:translateX(-50%);width:167px;height:50px}
.btn-yellow{background:var(--yellow);color:#2b2b22}
.btn-blue{background:var(--blue);color:var(--white)}

/* about */
.about{left:0;top:1131px;width:1200px;height:478px;overflow:hidden}
.about-photo{left:0;top:0;width:1200px;height:478px;background:linear-gradient(120deg,#b9bbbd 0%,#e7e4de 40%,#9a9996 70%,#6e5a48 100%)}
.about-band{left:0;top:0;width:1200px;height:478px}
.about h2{position:absolute;left:0;width:628px;text-align:center;font-family:'Montserrat',sans-serif;font-weight:700;color:var(--white);text-transform:uppercase}
.about .kicker{top:87px;font-size:25px;letter-spacing:1px}
.about .title{top:113px;font-size:38px;letter-spacing:2px}
.about p{position:absolute;left:66px;width:496px;top:175px;text-align:center;font-size:15px;line-height:25.2px;color:#eef7fc}
.about .btn{position:absolute;left:238px;top:352px;width:157px;height:49px;background:var(--pale);color:var(--blue);font-size:13px}

/* work */
.section-title{left:0;width:1200px;text-align:center;font-family:'Montserrat',sans-serif;font-weight:700;font-size:31px;letter-spacing:2px;color:var(--ink);text-transform:uppercase}
.work-tile{position:absolute}

/* testimonials */
.testimonials{left:0;top:2268px;width:1200px;height:502px;background:var(--yellow)}
.testimonials .photo{left:0;top:0;width:500px;height:502px;background:linear-gradient(135deg,#58c7c9 0%,#6bd1c8 30%,#f4e83b 55%,#f9e93a 100%)}
.testimonials h2{left:552px;top:102px;font-family:'Montserrat',sans-serif;font-weight:700;font-size:30px;letter-spacing:2px;color:#252419;text-transform:uppercase}
.quote{left:552px;top:160px;width:540px;font-family:'Arimo',sans-serif;font-size:20.5px;line-height:31.5px;color:#2d2b1d}
.qmark{font-family:Georgia,serif;font-weight:700;font-size:68px;color:#2d2b1d;line-height:1}
.author{left:553px;top:340px;font-family:'Montserrat',sans-serif;font-weight:700;font-size:17px;letter-spacing:1px;color:#2d2b1d;text-transform:uppercase}
.dots{left:553px;top:396px;display:flex;gap:9px}
.dots span{width:13px;height:13px;border-radius:50%;background:#8a8420}
.dots span.current{background:transparent;border:1.5px solid #6c6720}

/* estimate */
.estimate-intro{left:200px;top:2897px;width:800px;text-align:center;font-size:13.5px;line-height:23px;color:#6a6d72}
.field{position:absolute;height:50px;border:1.5px solid var(--line);padding:0 20px;display:flex;align-items:center;font-size:14.5px;color:#45484d}
.submit{left:522px;top:3119px;width:163px;height:49px;font-size:17px;letter-spacing:1.5px}

/* footer */
.site-footer{left:0;top:3242px;width:1200px;height:168px;background:var(--blue);color:var(--white)}
.footer-nav a{position:absolute;top:64px;font-family:'Montserrat',sans-serif;font-size:15px;letter-spacing:.6px;color:var(--white);text-decoration:none;text-transform:uppercase}
.copyright{left:126px;top:101px;font-family:'Montserrat',sans-serif;font-size:13px;color:var(--white)}
.contact-info{left:751px;top:62px;font-family:'Montserrat',sans-serif;font-size:14.5px;line-height:25px}
.contact-info div{display:flex;align-items:center;gap:6px}
.social{top:63px;width:31px;height:31px;border:1.5px solid var(--white);border-radius:50%}
</style>
</head>
<body>

<header class="site-header abs">
  <div class="brand abs">Tidewell Homecare</div>
  <nav class="main-nav">
    <a class="active" style="left:401px">Services</a>
    <a style="left:526px">About</a>
    <a style="left:629px">Reviews</a>
    <a style="left:751px">Blogs</a>
    <a style="left:850px">Contact</a>
  </nav>
  <div class="phone-btn abs">
    <svg width="17" height="17" viewBox="0 0 24 24"><path fill="#3a3218" d="M6.6 10.8a15.1 15.1 0 0 0 6.6 6.6l2.2-2.2c.3-.3.7-.4 1-.2 1.1.4 2.3.6 3.6.6.6 0 1 .4 1 1V20c0 .6-.4 1-1 1A17 17 0 0 1 3 4c0-.6.4-1 1-1h3.5c.6 0 1 .4 1 1 0 1.3.2 2.5.6 3.6.1.3 0 .7-.2 1z"/></svg>
    555-318-2047
  </div>
</header>

<section class="hero abs" role="img" aria-label="Bright, tidy living room with grey sofa and open white kitchen">
</section>
<svg class="hero-arrow abs" style="left:22px" width="26" height="44" viewBox="0 0 26 44"><path d="M22 4 6 22l16 18" fill="none" stroke="#fff" stroke-width="4"/></svg>
<svg class="hero-arrow abs" style="left:1140px" width="26" height="44" viewBox="0 0 26 44"><path d="M4 4l16 18L4 40" fill="none" stroke="#fff" stroke-width="4"/></svg>
<div class="hero-frame abs"></div>
<div class="hero-panel abs">
  <h1>Welcome to Tidewell<br>Homecare</h1>
  <p>Lorem ipsum dolor sit amet consect etuer adipiscing elit Nam cursus Morbi ut mi Nullam enim</p>
  <svg style="margin-top:8px" width="34" height="20" viewBox="0 0 34 20"><path d="M3 3l14 13L31 3" fill="none" stroke="#1e1e18" stroke-width="4"/></svg>
</div>

<article class="card commercial abs">
  <svg width="58" height="58" viewBox="0 0 58 58" fill="none" stroke="#f0d81e" stroke-width="2.2">
    <rect x="6" y="4" width="26" height="17" rx="1"/><path d="M14 21v5h10v-5"/>
    <path d="M2 28h54v8H2zM6 36v20M52 36v20M38 36v16h14"/><rect x="38" y="14" width="10" height="14"/>
  </svg>
  <h2>Commercial Cleaning</h2>
  <p>Augiat in pede Fusce tellus Sed metus augue convallis et vehicula ut pulvinar eu ante Integer orci tellus tristique vitae consequat nec</p>
  <div class="btn btn-yellow">View Services</div>
</article>

<article class="card residential abs">
  <svg width="68" height="50" viewBox="0 0 68 50" fill="none" stroke="#2f95d2" stroke-width="2.2">
    <path d="M10 20V8a4 4 0 0 1 4-4h40a4 4 0 0 1 4 4v12"/><path d="M34 4v22"/>
    <rect x="2" y="18" width="9" height="20" rx="3"/><rect x="57" y="18" width="9" height="20" rx="3"/>
    <path d="M11 26h46v12H11zM8 38v6M60 38v6"/>
  </svg>
  <h2>Residential Cleaning</h2>
  <p>Augiat in pede Fusce tellus Sed metus augue convallis et vehicula ut pulvinar eu ante Integer orci tellus tristique vitae consequat nec</p>
  <div class="btn btn-blue">View Services</div>
</article>

<section class="about abs">
  <div class="about-photo abs" role="img" aria-label="Modern white kitchen with marble island, pendant lamps and steel fridge"></div>
  <svg class="about-band abs" width="1200" height="478" viewBox="0 0 1200 478">
    <defs><linearGradient id="aboutBlue" x1="0" y1="0" x2="1" y2="1"><stop offset="0" stop-color="#2c8fd0"/><stop offset="1" stop-color="#66bbe4"/></linearGradient></defs>
    <polygon points="0,0 726,0 535,478 0,478" fill="url(#aboutBlue)"/>
  </svg>
  <h2 class="kicker">About Tidewell</h2>
  <h2 class="title">Homecare</h2>
  <p>Augiat in pede Fusce tellus Sed metus augue convallis et vehicula ut pulvinar eu ante Integer orci tellus tristique vitae consequat nec mauris viverra in gravida eu mattis in ante Morbi eget arcurmentum vel congue id euismod in elit Fusce ultricies orci ac feugiat suscipit leo massa sodales velit et scelerisque mi tortor at ipsum Proin orci odio commodo ac gravida non tristique vel te Curabitur iaculis</p>
  <div class="btn">Learn More</div>
</section>

<h2 class="section-title abs" style="top:1659px">Our Work</h2>
<div class="work-tile" style="left:0;top:1739px;width:387px;height:253px;background:linear-gradient(135deg,#d9d7d2,#8b8178 60%,#5b4f47)" role="img" aria-label="Kitchen with wooden island and bar stools"></div>
<div class="work-tile" style="left:400px;top:1739px;width:389px;height:253px;background:linear-gradient(180deg,#d8d8d2,#f3f3f0 55%,#ffffff)" role="img" aria-label="Carpet being deep cleaned with a vacuum nozzle"></div>
<div class="work-tile" style="left:808px;top:1739px;width:389px;height:253px;background:linear-gradient(135deg,#f2f2f0,#d9d6d0 50%,#7e6854)" role="img" aria-label="Open plan kitchen and dining room"></div>
<div class="work-tile" style="left:0;top:2005px;width:387px;height:253px;background:linear-gradient(135deg,#c77a45,#d9a878 45%,#bdb6a5)" role="img" aria-label="Living room with brick wall and colourful cushions"></div>
<div class="work-tile" style="left:400px;top:2005px;width:389px;height:253px;background:linear-gradient(180deg,#e8ecef,#c9cfd3 50%,#8f959a)" role="img" aria-label="Bright open office with desks and chairs"></div>
<div class="work-tile" style="left:808px;top:2005px;width:389px;height:253px;background:linear-gradient(180deg,#e6e6e4,#cfcfcc 60%,#b0b0ad)" role="img" aria-label="Grey sofa in a minimal room"></div>

<section class="testimonials abs">
  <div class="photo abs" role="img" aria-label="Rubber gloves, sponges, brushes and spray bottle on yellow background"></div>
  <h2 class="abs">Testimonials</h2>
  <span class="qmark abs" style="left:509px;top:162px">&ldquo;</span>
  <p class="quote abs">Augiat in pede Fusce tellus Sed metus augue convallis et vehicula ut pulvinar eu ante Integer orci tellus tristique vitae consequat nec mauris viverra in gravida eu mattis in ante Morbi eget arcurmentum vel congue id euismod in elit Fusce ultricies orci ac feugiat suscipit leo!</p>
  <span class="qmark abs" style="left:916px;top:296px">&rdquo;</span>
  <div class="author abs">By Author Name</div>
  <div class="dots abs"><span class="current"></span><span></span><span></span><span></span></div>
</section>

<h2 class="section-title abs" style="top:2846px">Free Estimate</h2>
<p class="estimate-intro abs">Augiat in pede Fusce tellus Sed metus augue convallis et vehicula ut pulvinar eu ante Integer orci tellus tristique vitae consequat nec mauris viverra in gravida eu mattis in ante Morbi eget arcurmentu</p>
<form>
  <div class="field" style="left:93px;top:2968px;width:249px">Name *</div>
  <div class="field" style="left:354px;top:2968px;width:249px">Email *</div>
  <div class="field" style="left:615px;top:2968px;width:249px">City *</div>
  <div class="field" style="left:873px;top:2968px;width:249px">Area Sq ft *</div>
  <div class="field" style="left:93px;top:3034px;width:249px">Property Type*</div>
  <div class="field" style="left:354px;top:3034px;width:249px">Type of Cleaning*</div>
  <div class="field" style="left:615px;top:3034px;width:249px">Select Date*</div>
  <div class="field" style="left:873px;top:3034px;width:249px">Select Time*</div>
  <div class="submit btn btn-blue abs">Submit</div>
</form>

<footer class="site-footer abs">
  <nav class="footer-nav">
    <a style="left:126px">Home</a>
    <a style="left:212px">Services</a>
    <a style="left:326px">About</a>
    <a style="left:420px">Reviews</a>
    <a style="left:531px">Blogs</a>
    <a style="left:622px">Contact</a>
  </nav>
  <div class="copyright abs">&copy; 2020 Company Name | All Rights Reserved</div>
  <div class="contact-info abs">
    <div><svg width="13" height="16" viewBox="0 0 12 16"><path fill="#fff" d="M6 0a6 6 0 0 0-6 6c0 4.5 6 10 6 10s6-5.5 6-10a6 6 0 0 0-6-6zm0 8.5A2.5 2.5 0 1 1 6 3.5a2.5 2.5 0 0 1 0 5z"/></svg>42 Harbor Lane #B</div>
    <div style="padding-left:19px">Texas 75001 TX</div>
    <div><svg width="13" height="13" viewBox="0 0 24 24"><path fill="#fff" d="M6.6 10.8a15.1 15.1 0 0 0 6.6 6.6l2.2-2.2c.3-.3.7-.4 1-.2 1.1.4 2.3.6 3.6.6.6 0 1 .4 1 1V20c0 .6-.4 1-1 1A17 17 0 0 1 3 4c0-.6.4-1 1-1h3.5c.6 0 1 .4 1 1 0 1.3.2 2.5.6 3.6.1.3 0 .7-.2 1z"/></svg>(555) 604 7781</div>
  </div>
  <div class="social abs" style="left:974px" aria-label="Social link"></div>
  <div class="social abs" style="left:1009px" aria-label="Social link"></div>
  <div class="social abs" style="left:1045px" aria-label="Social link"></div>
</footer>

</body>
</html>
```